QVR business card

Need a business card for a company that provides instructional design and elearning development services. The website is here: http://quorvane.studio/

I'm attaching a current logo, as well as the old business card design. While I like to keep it clean, the old design is too simplistic for my liking. The only idea I want to reuse from the old design is placing industry jargon on the back of the card, just need a better way to present it. But if you have other ideas for the back--feel free to experiment.

Please use the colors complementary to the color we have on the website. Thank you!

```html
<!DOCTYPE html>
<html lang="en">
<head>
<meta charset="utf-8">
<title>QVR Business Card</title>
<link rel="stylesheet" href="https://fonts.googleapis.com/css2?family=Arimo:wght@400;700&family=Montserrat:wght@500;600;700&family=Roboto:wght@400&display=swap">
<style>
  :root {
    --stage: #2b2b2d;
    --teal: #17a89b;
    --teal-deep: #12998d;
    --gold: #d8c58c;
    --white: #ffffff;
    --ink: #2e2e2e;
  }
  * { margin: 0; padding: 0; box-sizing: border-box; }
  html, body {
    width: 1200px; height: 900px; overflow: hidden;
    background: var(--stage);
  }
  .canvas { position: relative; width: 1200px; height: 900px; }
  .card {
    position: absolute; left: 280px; width: 640px; height: 366px;
    box-shadow: 0 14px 30px rgba(0,0,0,.45);
    overflow: hidden;
  }
  /* Back */
  .card-back {
    top: 64px;
    background: linear-gradient(135deg, var(--teal) 0%, var(--teal-deep) 100%);
    padding: 48px 0 0 58px;
  }
  .services {
    list-style: none;
    font-family: "Arimo", Arial, sans-serif;
    font-size: 33px; line-height: 38.5px;
    color: var(--white); letter-spacing: 1.5px;
    text-transform: uppercase;
    white-space: nowrap;
  }
  .services .invite { color: var(--gold); font-weight: 700; }
  /* Front */
  .card-front { top: 470px; background: var(--white); }
  .brand {
    position: absolute; left: 58px; top: 96px;
    display: flex; align-items: center; gap: 14px;
  }
  .brand-mark { width: 40px; height: 40px; background: var(--teal); }
  .brand-name {
    font-family: "Montserrat", sans-serif; font-weight: 700;
    font-size: 46px; color: var(--teal); letter-spacing: 2px;
  }
  .person {
    position: absolute; left: 58px; top: 222px;
    font-family: "Montserrat", sans-serif; font-weight: 600;
    font-size: 21px; color: var(--teal); letter-spacing: .5px;
    text-transform: uppercase;
  }
  .contacts {
    position: absolute; left: 58px; top: 262px;
    list-style: none;
    font-family: "Roboto", sans-serif; font-size: 16px;
    color: var(--ink); line-height: 24px;
  }
  .contacts li { display: flex; align-items: center; gap: 10px; }
  .contacts svg { width: 13px; height: 13px; flex: none; }
  .accent-bar {
    position: absolute; left: 0; bottom: 0;
    width: 16px; height: 110px; background: var(--gold);
    border-top-right-radius: 10px;
  }
</style>
</head>
<body>
<main class="canvas">
  <section class="card card-back" aria-label="Card back">
    <ul class="services">
      <li>Microlearning cmi5 AR/VR</li>
      <li>Performance support UX</li>
      <li>Simulations assessment</li>
      <li>Onboarding storyboards</li>
      <li>Branching scenarios LXP</li>
      <li>Virtual training video</li>
      <li class="invite">What shall we build?</li>
    </ul>
  </section>

  <section class="card card-front" aria-label="Card front">
    <div class="brand">
      <span class="brand-mark" aria-hidden="true"></span>
      <span class="brand-name">QVR</span>
    </div>
    <p class="person">Marten Eloway</p>
    <ul class="contacts">
      <li>
        <svg viewBox="0 0 24 24" aria-hidden="true"><path fill="#17a89b" d="M6.6 10.8a15.1 15.1 0 0 0 6.6 6.6l2.2-2.2a1 1 0 0 1 1-.25 11.4 11.4 0 0 0 3.6.57 1 1 0 0 1 1 1V20a1 1 0 0 1-1 1A17 17 0 0 1 3 4a1 1 0 0 1 1-1h3.5a1 1 0 0 1 1 1c0 1.25.2 2.45.57 3.6a1 1 0 0 1-.25 1z"/></svg>
        555-014-2286
      </li>
      <li>
        <svg viewBox="0 0 24 24" aria-hidden="true"><g fill="none" stroke="#17a89b" stroke-width="2"><circle cx="12" cy="12" r="9"/><path d="M3 12h18M12 3c3 3 3 15 0 18M12 3c-3 3-3 15 0 18"/></g></svg>
        www.quorvane.studio
      </li>
      <li>
        <svg viewBox="0 0 24 24" aria-hidden="true"><g fill="none" stroke="#17a89b" stroke-width="2"><rect x="3" y="5" width="18" height="14"/><path d="M3 5l9 8 9-8"/></g></svg>
        meloway@quorvane.studio
      </li>
    </ul>
    <span class="accent-bar" aria-hidden="true"></span>
  </section>
</main>
</body>
</html>
```